Seeking funky, innovative business cards

I am looking to refresh our current business cards to something more engaging, visual and impactful. We are a management consultancy firm, see website (www.larkstone-partners.com.au). I've included our colour scheme, sample of the slides we use and our old business cards. We would like our cards to have icons. The card should display:- Name- Title- Mobile number- Address- Email address- Website - Company logo- Our purpose statement "we shape workplaces people love to join"

Contact Information for Business Card

Brennan Ulfsson
Consultant
0468 927 341
Suite 12, 218 Wexley Street, Brindale 3187
brennan@larkstone-partners.com.au
www.larkstone-partners.com.au

Purpose statement "we shape workplaces people love to join"
LOGO available in google images

Font styles to use
Other font styles liked:
• Open Sans Light, Bebas Neue (open to other cool foints)

Colors
ffc214
5c5c5c
f5f5f5
fefefe

Requirements
Must have
• - Name
• - Title
• - Mobile number
• - Address
• - Email address
• - Website
• - Company logo
• - Our purpose statement "we shape workplaces people love to join"
Nice to have
• - Icons
• - Colour (see our colour scheme"

```html
<!DOCTYPE html>
<html lang="en">
<head>
<meta charset="utf-8">
<title>Larkstone Partners – Business Card</title>
<link rel="stylesheet" href="https://fonts.googleapis.com/css2?family=Open+Sans:ital,wght@0,300;0,400;0,600;1,700&display=swap">
<style>
  :root {
    --accent: #ffc214;
    --ink-light: #fefefe;
    --ink-soft: #f5f5f5;
    --grey: #5c5c5c;
    --card: #24272a;
    --backdrop: #3a3b3e;
  }
  * { box-sizing: border-box; margin: 0; padding: 0; }
  html, body {
    width: 1200px; height: 800px; overflow: hidden;
    background: var(--backdrop);
    font-family: "Open Sans", Arial, sans-serif;
    color: var(--ink-light);
  }
  .stage {
    width: 1200px; height: 800px;
    display: flex; align-items: center; justify-content: center; gap: 40px;
  }
  .card {
    position: relative;
    width: 550px; height: 320px;
    background: var(--card);
    box-shadow: 0 14px 30px rgba(0,0,0,.35);
    overflow: hidden;
  }
  .brand { display: flex; align-items: center; gap: 12px; }
  .brand-dot {
    width: 16px; height: 16px; border-radius: 50%;
    background: var(--accent);
  }
  .brand-dot.small { width: 12px; height: 12px; }
  .brand-name {
    font-weight: 300; color: var(--ink-light);
    letter-spacing: -1px; line-height: 1;
  }
  .card-front .brand { position: absolute; inset: 0; justify-content: center; }
  .card-front .brand-name { font-size: 68px; }
  .card-back .brand { position: absolute; right: 34px; top: 34px; }
  .card-back .brand-name { font-size: 46px; }

  .details {
    position: absolute; left: 34px; top: 92px; width: 320px;
  }
  .person-name {
    font-size: 19px; font-weight: 600; color: var(--ink-light); line-height: 24px;
  }
  .person-title {
    font-size: 14px; font-weight: 400; color: var(--accent); line-height: 19px;
  }
  .divider {
    border: none; border-top: 2px dotted var(--accent);
    margin: 7px 0; width: 230px;
  }
  .contact-list { list-style: none; }
  .contact-item {
    display: flex; align-items: center; gap: 8px;
    font-size: 12.5px; line-height: 19px; color: var(--ink-soft);
  }
  .contact-icon { width: 14px; height: 14px; flex: none; }
  .address {
    font-size: 12.5px; line-height: 18px; color: var(--ink-soft); font-style: normal;
  }
  .purpose {
    margin-top: 10px;
    font-size: 13px; line-height: 18px; font-weight: 700; font-style: italic;
    color: var(--ink-light); white-space: nowrap;
  }
</style>
</head>
<body>
<main class="stage">
  <section class="card card-front" aria-label="Card front">
    <div class="brand">
      <span class="brand-dot" aria-hidden="true"></span>
      <span class="brand-name">Larkstone</span>
    </div>
  </section>

  <section class="card card-back" aria-label="Card back">
    <div class="brand">
      <span class="brand-dot small" aria-hidden="true"></span>
      <span class="brand-name">Larkstone</span>
    </div>

    <div class="details">
      <h1 class="person-name">Brennan Ulfsson</h1>
      <p class="person-title">Consultant</p>
      <hr class="divider">
      <ul class="contact-list">
        <li class="contact-item">
          <svg class="contact-icon" viewBox="0 0 16 16" aria-hidden="true">
            <circle cx="8" cy="8" r="8" fill="var(--accent)"/>
            <path d="M5.2 4.2l1.5 0 .6 2-1 .8a5 5 0 0 0 2.7 2.7l.8-1 2 .6 0 1.5c-.4.6-1 .8-1.6.7A7 7 0 0 1 4.5 5.8c-.1-.6.1-1.2.7-1.6z" fill="var(--card)"/>
          </svg>
          0468 927 341
        </li>
        <li class="contact-item">
          <svg class="contact-icon" viewBox="0 0 16 16" aria-hidden="true">
            <circle cx="8" cy="8" r="8" fill="var(--accent)"/>
            <rect x="4" y="5.2" width="8" height="5.6" rx=".6" fill="var(--card)"/>
            <path d="M4.3 5.6 8 8.4l3.7-2.8" stroke="var(--accent)" stroke-width=".9" fill="none"/>
          </svg>
          brennan@larkstone-partners.com.au
        </li>
        <li class="contact-item">
          <svg class="contact-icon" viewBox="0 0 16 16" aria-hidden="true">
            <circle cx="8" cy="8" r="8" fill="var(--accent)"/>
            <g stroke="var(--card)" stroke-width=".9" fill="none">
              <circle cx="8" cy="8" r="4.2"/>
              <ellipse cx="8" cy="8" rx="1.8" ry="4.2"/>
              <path d="M3.8 8h8.4"/>
            </g>
          </svg>
          www.larkstone-partners.com.au
        </li>
      </ul>
      <hr class="divider">
      <address class="address">Suite 12, 218 Wexley Street<br>Brindale 3187</address>
      <p class="purpose">we shape workplaces people love to join</p>
    </div>
  </section>
</main>
</body>
</html>
```